Event Center Website

We need a new website design for an upscale event center in Reno, Nevada. The building hosts everything from weddings to corporate events to funerals and it competitively more expensive. The overall look and feel is consistent with a Lake Tahoe aesthetic. The current site can be viewed at www.themaplehallevents.com. They are looking for a major upgrade. A sample site they like is www.cliffsidelodgestay.com. We have new photography available (some attached). The site should be very visual. A site map is attached as well for direction on what elements the site should include as well as labels for navigation. I am looking for a home page and sample interior page. Any questions, let me know. Thanks.
Updates

I have added some photography of the center itself for use rather than stock photography. Thanks!

Target Market(s)

Brides, professionals, high-income

Industry/Entity Type

Building

Requirements
Must have
• See site map

```html
<!DOCTYPE html>
<html lang="en">
<head>
<meta charset="utf-8">
<title>Maple Hall at Stoneridge – About Us</title>
<link href="https://fonts.googleapis.com/css2?family=Della+Respira&family=Delius&family=Roboto+Condensed:wght@400;500&family=Ubuntu:wght@500&display=swap" rel="stylesheet">
<style>
  :root{
    --header-bg:#eeece8;
    --brown:#4a2a18;
    --nav-text:#3b2616;
    --orange:#d97a22;
    --white:#ffffff;
    --cream:#f4ecdf;
    --footer-dark:#1e130c;
    --footer-mid:#3a2416;
    --board-light:#9a6a40;
    --board-dark:#7a4e2c;
    --board-text:#2a1608;
  }
  *{box-sizing:border-box;margin:0;padding:0}
  html,body{width:1200px;height:807px;overflow:hidden;background:var(--header-bg)}
  .page{position:relative;width:1200px;height:807px;overflow:hidden}

  .site-header{position:absolute;left:0;top:0;width:1200px;height:94px;
    background:radial-gradient(ellipse at 50% 0%,#fbfaf8 0%,var(--header-bg) 70%,#e2dfd9 100%)}
  .brand{position:absolute;left:124px;top:20px;height:60px;display:flex;align-items:center;gap:10px}
  .brand-mark{width:22px;height:22px;background:var(--brown)}
  .brand-name{font-family:"Delius",cursive;font-size:28px;color:var(--brown);white-space:nowrap}
  .main-nav{position:absolute;right:124px;top:42px;display:flex;gap:5px}
  .main-nav a{font-family:"Roboto Condensed",sans-serif;font-weight:500;font-size:14.5px;
    color:var(--nav-text);text-decoration:none;padding:5px 8px;border-radius:3px;letter-spacing:.2px}
  .main-nav a.active{background:var(--orange);color:var(--brown)}

  .hero{position:absolute;left:0;top:94px;width:1200px;height:570px;
    background:linear-gradient(180deg,#2f6fc0 0%,#5d92d0 35%,#8c6a48 55%,#6b4a30 72%,#8f8a80 88%,#4a4a4a 100%)}
  .hero-line{position:absolute;background:rgba(40,28,20,.55);color:var(--white)}
  .hero-intro{left:124px;top:253px;height:52px;padding:0 6px;
    font-family:"Della Respira",serif;font-size:37px;line-height:52px;white-space:nowrap}
  .hero-title{left:124px;top:318px;height:50px;padding:0 6px;
    font-family:"Ubuntu",sans-serif;font-weight:500;font-size:37px;line-height:50px;letter-spacing:.5px}
  .hero-cta{position:absolute;left:125px;top:380px;width:209px;height:38px;background:var(--orange);
    color:var(--white);font-family:"Roboto Condensed",sans-serif;font-weight:500;font-size:14px;
    line-height:38px;text-align:center;text-decoration:none}

  .site-footer{position:absolute;left:0;top:664px;width:1200px;height:143px;
    background:linear-gradient(90deg,var(--footer-dark) 0%,var(--footer-mid) 45%,#4a2e1a 60%,var(--footer-dark) 100%);
    border-top:3px solid #2a1a10}
  .address-sign{position:absolute;left:118px;top:-25px;width:201px;height:168px;
    background:linear-gradient(180deg,var(--board-light) 0%,var(--board-dark) 100%)}
  .sign-text{position:absolute;left:128px;font-family:"Delius",cursive;color:var(--board-text);white-space:nowrap;font-size:15.5px}
  .footer-links{position:absolute;left:425px;top:25px;list-style:none}
  .footer-links li{font-family:"Roboto Condensed",sans-serif;font-weight:500;font-size:15px;color:var(--white);
    height:21px;display:flex;align-items:center;gap:17px}
  .footer-links li span{color:var(--orange);font-size:14px}
  .contact{position:absolute;left:630px;font-family:"Delius",cursive;font-size:16px;color:var(--white);
    display:flex;align-items:center;gap:12px}
  .contact svg{flex:none}
  .tour{position:absolute;left:860px;top:22px;width:202px;text-align:center;
    font-family:"Delius",cursive;font-size:16.5px;line-height:23px;color:var(--white)}
  .tour svg{display:block;margin:6px auto 0}
  .copyright{position:absolute;left:0;width:1200px;top:111px;text-align:center;
    font-family:"Delius",cursive;font-size:12px;color:var(--cream)}
</style>
</head>
<body>
<div class="page">
  <header class="site-header">
    <div class="brand"><span class="brand-mark"></span><span class="brand-name">Maple Hall</span></div>
    <nav class="main-nav">
      <a href="#">HOME</a>
      <a href="#" class="active">ABOUT US</a>
      <a href="#">GALLERY</a>
      <a href="#">WEDDINGS</a>
      <a href="#">MEETINGS</a>
      <a href="#">OTHER EVENTS</a>
      <a href="#">CATERINGS</a>
    </nav>
  </header>

  <section class="hero" role="img" aria-label="Photograph of the timber-framed lodge-style event center entrance with stone walls and flower beds under a blue sky">
    <div class="hero-line hero-intro">Thank you for your interest in</div>
    <div class="hero-line hero-title">MAPLE HALL</div>
    <a href="#" class="hero-cta">SCHEDUAL AN APPOINTMENT</a>
  </section>

  <footer class="site-footer">
    <div class="address-sign" role="img" aria-label="Illustration of a rustic wooden signpost carrying the venue address"></div>
    <div class="sign-text" style="top:3px;font-size:16px">Maple Hall | Stoneridge</div>
    <div class="sign-text" style="top:26px">2270 Ridgeline Rd, Suite C</div>
    <div class="sign-text" style="top:49px">Carson, Nevada 89701</div>

    <ul class="footer-links">
      <li><span>»</span>FAQ</li>
      <li><span>»</span>TESTIMONIAL</li>
      <li><span>»</span>CONTACT US</li>
    </ul>

    <div class="contact" style="top:20px">
      <svg width="18" height="14" viewBox="0 0 18 14" aria-hidden="true"><rect width="18" height="14" rx="1" fill="var(--orange)"/><path d="M1 1l8 7 8-7" fill="none" stroke="var(--footer-dark)" stroke-width="1.6"/></svg>
      info@maplehallevents.com
    </div>
    <div class="contact" style="top:50px">
      <svg width="18" height="18" viewBox="0 0 18 18" aria-hidden="true"><rect width="18" height="18" rx="3" fill="var(--orange)"/><path d="M5 4c1 0 1.5 2 2 3l-1 1c.7 1.6 2 2.9 3.6 3.6l1-1c1 .5 3 1 3 2l-1 2C8 14 4 10 4 5z" fill="var(--footer-dark)"/></svg>
      +1.555.014.2287
    </div>

    <div class="tour">Click here to See Our<br>Virtual Tour
      <svg width="38" height="26" viewBox="0 0 38 26" aria-hidden="true"><path d="M9 25a8 8 0 0 1-1-16 11 11 0 0 1 21 0 8 8 0 0 1 1 16z" fill="var(--orange)"/><path d="M19 8v10M14 13l5 5 5-5" fill="none" stroke="var(--footer-dark)" stroke-width="2.4"/></svg>
    </div>

    <div class="copyright">All rights reserved ©2013-2014</div>
  </footer>
</div>
</body>
</html>
```